Website Redesign for Non-Profit Ministry & Church

NOTE: Please do not contact me privately — all private inquiries will be ignored.

Individuals seeking spiritual healing, community connection, ministry support and journal-based encounters.

Description of What’s Needed

We need a clean, fresh, inviting website that encourages engagement and connection. The site should feel warm and accessible, draw people in, and clearly present who we are, what we offer, and how visitors can participate. The layout should be straightforward, with well-structured pages (no overlapping objects, minimal layering complexity) and easy to navigate. Use only Google Fonts. All stock photos must be sourced from royalty-free sites and include proper attribution. We will not include a search feature.

Pages to Create
1. Home Page – impactful hero area, clear call-to-action, visual story of ministry, giving/gathering invitation.
2. About Us – vision, mission, leadership, testimonies, history.
3. Meetings & Events – upcoming gatherings, schedule, how to attend, sign-up or interest form.
4. Encounter: “Lanterns by the River” (book) – dedicated page for the book, overview, purchase link or details, journal prompts, imagery.
5. Healing Rooms / Ministry – explain ministry offerings, invite participation, testimonials or case-studies.
6. Live Stream & Links Page – page listing links for YouTube live stream, other platforms, archive links; simple layout.

Colour & Branding

Use colours that blend with our existing logo (attached). The palette should feel contemporary, welcoming, and aligned with ministry themes of restoration, healing and love. Ensure text, button and link colours maintain good contrast for accessibility.

Existing Content & Reference

Please gather available content from our current website in the attachment here for text, images and structure for reuse.

Imagery Guidelines

– Use original photos from our Facebook page or Google Location listing for building or people images when available.
– If generic images are used, ensure they depict appropriate ministry-related buildings or people (community, warm gathering) — avoid generic unrelated stock imagery.
– All photos must be royalty-free or have proper licensing and attribution.
– No overlapping objects or visual clutter; clean layouts with defined sections.

Additional Notes

– Integration: We currently utilise MailChimp for email communication; the design should include a connection/invite to subscribe (via MailChimp) but no blog page is required at this time.
– Payment/Giving: We accept PayPal and already have a giving portal; include clear donation/give buttons or calls-to-action linking to existing giving systems.
– No search function to be included.
– Layouts should avoid complex layering or overlapping elements—designers should work with distinct content blocks, clear visual hierarchy, and straightforward mobile-friendly structure.

Target Market(s)

Industry/Entity Type

Church/Religious institution

Number of Pages Required

5+ page

Requirements
Should not have
• search bar

```html
<!DOCTYPE html>
<html lang="en">
<head>
<meta charset="utf-8">
<title>Restored Hearts Rising</title>
<link href="https://fonts.googleapis.com/css2?family=Ubuntu:wght@400;500;700&family=Figtree:wght@400;500;600;700&display=swap" rel="stylesheet">
<style>
:root{
  --teal:#0ea59a;
  --teal-deep:#00a49a;
  --green:#1d6b4a;
  --purple:#5b2d91;
  --ink:#1c1c1c;
  --white:#ffffff;
  --black:#000000;
}
*{box-sizing:border-box;margin:0;padding:0}
html,body{width:1200px;height:2373px;overflow:hidden}
body{font-family:'Figtree',sans-serif;color:var(--ink);background:var(--white);position:relative}
.heading{font-family:'Ubuntu',sans-serif}
.site-header{position:absolute;top:0;left:0;width:1200px;height:86px;background:var(--white)}
.brand{position:absolute;left:67px;top:24px;display:flex;align-items:center;gap:10px;font-family:'Ubuntu',sans-serif;font-weight:700;font-size:17px;line-height:18px;color:var(--teal);width:150px}
.brand-dot{width:34px;height:34px;border-radius:50%;background:var(--teal);flex:none}
.nav{position:absolute;top:34px;font-family:'Ubuntu',sans-serif;font-size:15px;color:#333}
.nav.active{color:var(--teal);font-weight:500}
.contact-box{position:absolute;left:1012px;top:0;width:188px;height:86px;background:var(--purple);color:var(--white);text-align:center;font-family:'Ubuntu',sans-serif}
.contact-box .lbl{font-size:17px;font-weight:500;margin-top:15px}
.contact-box .num{font-size:20px;font-weight:700;margin-top:6px}
.hero{position:absolute;top:86px;left:0;width:1200px;height:591px;background:linear-gradient(180deg,#3d3a4a 0%,#7b4a3e 25%,#d66a26 45%,#e89a2c 55%,#8a3b1e 75%,#4a2a22 100%)}
.hero-title{position:absolute;left:105px;top:104px;font-size:86px;font-weight:700;line-height:94px;color:var(--white)}
.hero-sub{position:absolute;left:112px;top:293px;width:560px;font-size:21px;font-weight:600;line-height:43.5px;color:var(--white)}
.btn{position:absolute;height:55px;border-radius:28px;color:var(--white);font-family:'Ubuntu',sans-serif;font-weight:700;font-size:17px;display:flex;align-items:center;padding-left:70px}
.btn::before{content:"";position:absolute;left:26px;top:17px;width:22px;height:22px;border-radius:50%;border:2px solid var(--white)}
.btn-teal{background:var(--teal)}
.btn-purple{background:var(--purple)}
.about-photo{position:absolute;left:112px;top:778px;width:359px;height:461px;border-radius:30px;background:linear-gradient(135deg,#7d8aa8 0%,#c9b7a6 40%,#5a5f80 70%,#3b2f5c 100%)}
.about-title{position:absolute;left:558px;top:780px;width:520px;font-size:43px;font-weight:700;line-height:56px;color:var(--green)}
.about-title .p{color:var(--purple)}
.about-title .t{color:var(--teal)}
.about-mark{display:inline-block;width:50px;height:50px;border-radius:50%;border:3px solid var(--teal);vertical-align:-6px;margin-right:20px}
.about-text{position:absolute;left:559px;top:893px;width:535px;font-size:15px;line-height:30px;color:#222}
.gather{position:absolute;top:1343px;left:0;width:1200px;height:554px;background:var(--teal-deep)}
.gather-photo{position:absolute;left:470px;top:0;width:730px;height:554px;background:linear-gradient(90deg,var(--teal-deep) 0%,rgba(120,110,120,.6) 35%,#8c8590 60%,#6a5d6a 100%)}
.gather-title{position:absolute;left:112px;top:70px;font-size:41px;font-weight:700;color:var(--white);display:flex;align-items:center;gap:22px}
.gather-title span.mk{width:56px;height:52px;border-radius:50%;border:3px solid var(--white)}
.gather-lead{position:absolute;left:112px;top:135px;width:540px;font-size:21px;font-weight:700;line-height:35px;color:var(--white)}
.gather-text{position:absolute;left:112px;top:284px;width:540px;font-size:15px;line-height:30px;color:var(--white)}
.footer{position:absolute;top:1897px;left:0;width:1200px;height:476px;background:var(--black);color:var(--white)}
.f-brand{position:absolute;left:112px;top:76px;display:flex;align-items:center;gap:14px;font-family:'Ubuntu',sans-serif;font-weight:700;font-size:30px;line-height:30px;color:var(--teal);width:240px}
.f-brand .dot{width:100px;height:100px;border-radius:50%;border:4px solid var(--teal);flex:none}
.social{position:absolute;left:112px;top:221px;width:32px;height:32px;border-radius:50%;background:var(--white)}
.f-h{position:absolute;top:84px;font-family:'Figtree',sans-serif;font-weight:700;font-size:21px}
.email-field{position:absolute;left:383px;top:129px;width:237px;height:48px;border-radius:24px;background:var(--white);color:#777;font-size:14px;padding:16px 0 0 22px}
.subscribe{position:absolute;left:382px;top:197px;width:188px;height:51px;border-radius:26px;background:var(--teal);font-weight:700;font-size:17px;text-align:center;line-height:51px}
.c-row{position:absolute;left:651px;display:flex;gap:12px;font-size:15px;line-height:28px}
.c-icon{width:33px;height:33px;border-radius:4px;background:var(--white);flex:none;display:flex;align-items:center;justify-content:center}
.links{position:absolute;left:945px;top:123px;list-style:none;font-size:15px}
.links li{height:34.5px;display:flex;align-items:center;gap:10px}
.rule{position:absolute;left:112px;top:376px;width:976px;height:1px;background:#555}
.copy{position:absolute;top:420px;width:1200px;text-align:center;font-size:13px;font-weight:600}
</style>
</head>
<body>
<header class="site-header">
  <div class="brand"><span class="brand-dot"></span>Restored Hearts Rising</div>
  <span class="nav active" style="left:252px">Home</span>
  <span class="nav" style="left:340px">About Us</span>
  <span class="nav" style="left:455px">Meetings &amp; Events</span>
  <span class="nav" style="left:634px">Encounter</span>
  <span class="nav" style="left:753px">Healing Rooms</span>
  <span class="nav" style="left:908px">Live Stream</span>
  <div class="contact-box"><div class="lbl">Contact Us</div><div class="num">+1 555-012-4410</div></div>
</header>

<section class="hero" role="img" aria-label="Sunset over canyon cliffs with a cross silhouetted against glowing clouds">
  <h1 class="hero-title heading">Restored Hearts<br>Rising</h1>
  <p class="hero-sub">Honoring God’s presence by loving the broken, saving the lost, and healing the hurting through the demonstration of His power.</p>
  <div class="btn btn-teal" style="left:112px;top:437px;width:189px">Get Started</div>
</section>

<div class="about-photo" role="img" aria-label="Portrait of the ministry couple in front of a stained glass window"></div>
<h2 class="about-title heading"><span class="about-mark"></span>About <span class="p">Restored</span> <span class="t">Hearts Rising</span></h2>
<div class="about-text">
  <p>Daniel and Lena Grace have been married for 42 years and have two adult children. They both grew up in southern Illinois. Their desire is to share the love of Christ with others. They have numerous stories to share about the many ways they have seen God move in their lives as well as the lives of others.</p>
  <p style="margin-top:30px">They believe in the manifestation of God’s power through signs and wonders. They have not only witnessed God’s power through signs and wonders them they have also experienced His miraculous healing touch personally.</p>
</div>
<div class="btn btn-teal" style="left:559px;top:1154px;width:189px">Read More</div>

<section class="gather">
  <div class="gather-photo" role="img" aria-label="Ministry couple leading worship with musicians in a church hall"></div>
  <h2 class="gather-title heading"><span class="mk"></span>Gathering Invitation</h2>
  <p class="gather-lead">If you are hosting an event at your church or ministry, as you prayerfully seek the Lord for guidance review these thoughts regarding Lena Grace &amp; Daniel Halvorsen and their ministry.</p>
  <p class="gather-text">I have served in church leadership with Lena and Daniel for several years, and I do not know of a more balanced and powerful ministry of miracles and healings. They are activators not only of supernatural demonstrations but of supernatural compassion.</p>
  <div class="btn btn-purple" style="left:112px;top:433px;width:190px">Read More</div>
</section>

<footer class="footer">
  <div class="f-brand"><span class="dot"></span>Restored Hearts Rising</div>
  <div class="social" aria-label="Social link"></div>
  <h3 class="f-h" style="left:388px">Join our Newletter</h3>
  <div class="email-field">Enter The Email</div>
  <div class="subscribe">Subscribe</div>
  <h3 class="f-h" style="left:653px">Contact Us</h3>
  <div class="c-row" style="top:130px"><span class="c-icon"><svg width="14" height="18" viewBox="0 0 14 18"><path d="M7 0a7 7 0 0 0-7 7c0 5 7 11 7 11s7-6 7-11a7 7 0 0 0-7-7zm0 9.5A2.5 2.5 0 1 1 7 4.5a2.5 2.5 0 0 1 0 5z" fill="#000"/></svg></span><span>214 Cedar Hollow Lane,<br>Fairview, IL, US</span></div>
  <div class="c-row" style="top:204px"><span class="c-icon"><svg width="16" height="16" viewBox="0 0 16 16"><path d="M3 1l3 3-2 2c1 2 3 4 6 6l2-2 3 3-2 2C7 15 1 9 1 3z" fill="#000"/></svg></span><span>+1 555-012-4410</span></div>
  <div class="c-row" style="top:272px"><span class="c-icon"><svg width="16" height="12" viewBox="0 0 16 12"><rect width="16" height="12" rx="1" fill="#000"/><path d="M1 1l7 6 7-6" stroke="#fff" stroke-width="1.5" fill="none"/></svg></span><span>hello@restoredheartsrising.org</span></div>
  <h3 class="f-h" style="left:945px">Quick Link</h3>
  <ul class="links">
    <li><svg width="13" height="12" viewBox="0 0 13 12"><path d="M0 6h11M6 1l5 5-5 5" stroke="#fff" stroke-width="2" fill="none"/></svg>Home</li>
    <li><svg width="13" height="12" viewBox="0 0 13 12"><path d="M0 6h11M6 1l5 5-5 5" stroke="#fff" stroke-width="2" fill="none"/></svg>About</li>
    <li><svg width="13" height="12" viewBox="0 0 13 12"><path d="M0 6h11M6 1l5 5-5 5" stroke="#fff" stroke-width="2" fill="none"/></svg>Meetings &amp; Events</li>
    <li><svg width="13" height="12" viewBox="0 0 13 12"><path d="M0 6h11M6 1l5 5-5 5" stroke="#fff" stroke-width="2" fill="none"/></svg>Encounter</li>
    <li><svg width="13" height="12" viewBox="0 0 13 12"><path d="M0 6h11M6 1l5 5-5 5" stroke="#fff" stroke-width="2" fill="none"/></svg>Contact Us</li>
  </ul>
  <div class="rule"></div>
  <p class="copy">Copyrights@2025.Restored Hearts Rising.All Rights Reserved</p>
</footer>
</body>
</html>
```